Brightway Haul & Upkeep Services, are a company that offers a 'one stop shop' pre-move clean up a

I have already selected a logo which I would like on the front of the business cards along with phone numbers, web address and email which are:
0487650392
www.brightwayhaul.com.au
brightwayhaulandupkeep@mailbox.example

On the back of the card I would like to list some of the types of service we offer (clean - move - repairs/maintenance) which are:
CLEAN - windows, gutters, solar panels, driveways/paths, carpets.
MOVE - Small/medium size house/office moves, large item pick-up & delivery, yard clean-up and removal.
General maintenance and repairs.

I would like the blue logo on a gray background.

Thanks

```html
<!DOCTYPE html>
<html lang="en">
<head>
<meta charset="utf-8">
<title>Brightway Haul &amp; Upkeep Services – Business Cards</title>
<link rel="stylesheet" href="https://fonts.googleapis.com/css2?family=Open+Sans:wght@400;600;700;800&display=swap">
<style>
  :root {
    --backdrop: #e9e7e4;
    --card-light: #e6e7e9;
    --card-mid: #c9cacd;
    --card-edge: #a9abaf;
    --brand-blue: #2168b8;
    --ink: #1f1f22;
    --swoosh-dark: #1b1a1c;
    --white: #ffffff;
  }
  * { margin: 0; padding: 0; box-sizing: border-box; }
  html, body {
    width: 1200px;
    height: 1085px;
    overflow: hidden;
    background: var(--backdrop);
    font-family: "Open Sans", Arial, sans-serif;
  }
  .stage { position: relative; width: 1200px; height: 1085px; }

  .card {
    position: absolute;
    width: 818px;
    height: 467px;
    border-radius: 24px;
    overflow: hidden;
    background: radial-gradient(ellipse 70% 80% at 40% 25%, var(--card-light) 0%, var(--card-mid) 65%, var(--card-edge) 100%);
    box-shadow: 0 0 0 1px rgba(0,0,0,0.35);
  }
  .card--front { left: 58px; top: 52px; }
  .card--back { left: 333px; top: 560px; }

  .brand-name {
    position: absolute;
    left: 0; right: 0;
    text-align: center;
    color: var(--brand-blue);
    font-weight: 800;
    font-size: 46px;
    line-height: 1.12;
    letter-spacing: 0.5px;
  }
  .card--front .brand-name { top: 118px; padding-left: 0; left: -10px; }
  .card--back .brand-name { top: 110px; left: 10px; }

  .contact {
    position: absolute;
    left: 0; right: 0;
    display: flex;
    align-items: center;
    justify-content: center;
    gap: 10px;
    color: var(--ink);
  }
  .contact svg { flex: none; }
  .contact--phone { top: 270px; font-size: 28px; left: -10px; }
  .contact--email { top: 313px; font-size: 21px; left: -10px; }

  .front-waves { position: absolute; left: 0; bottom: 0; width: 818px; height: 467px; }

  .website {
    position: absolute;
    left: 45px;
    top: 422px;
    color: var(--white);
    font-size: 21px;
    letter-spacing: 4.2px;
  }

  .services-title {
    position: absolute;
    left: 0; right: 0;
    top: 278px;
    text-align: center;
    color: var(--brand-blue);
    font-weight: 700;
    font-size: 32px;
    letter-spacing: 3px;
  }
  .services-list {
    position: absolute;
    left: 0; right: 0;
    top: 348px;
    list-style: none;
    text-align: center;
    color: var(--ink);
    font-weight: 600;
    font-size: 24px;
    line-height: 42px;
  }
  .services-list li { display: inline-block; margin: 0 10px; }
  .services-list li::before {
    content: "";
    display: inline-block;
    width: 8px; height: 8px;
    border-radius: 50%;
    background: var(--brand-blue);
    margin-right: 10px;
    vertical-align: 5px;
  }
  .services-list .wide { display: block; }
</style>
</head>
<body>
<main class="stage">

  <section class="card card--front" aria-label="Business card front">
    <h1 class="brand-name">Brightway Haul<br>&amp; Upkeep Services</h1>

    <p class="contact contact--phone">
      <svg width="22" height="22" viewBox="0 0 22 22" aria-hidden="true">
        <circle cx="11" cy="11" r="9.5" fill="none" stroke="#2168b8" stroke-width="1.6"/>
        <path d="M8 6c-1 1-1.5 2.5-.5 5s3 4.5 5 5c1 .3 2 0 2.5-.8l-1.8-1.8-1.4.8c-1.2-.6-2.3-1.8-2.9-3l.8-1.4L8 6z" fill="#2168b8"/>
      </svg>
      0487650392
    </p>
    <p class="contact contact--email">
      <svg width="20" height="14" viewBox="0 0 20 14" aria-hidden="true">
        <rect x="0.5" y="2" width="19" height="11.5" rx="1" fill="#2168b8"/>
        <path d="M1 3l9 6 9-6" fill="none" stroke="#fff" stroke-width="1.4"/>
      </svg>
      brightwayhaulandupkeep@mailbox.example
    </p>

    <svg class="front-waves" viewBox="0 0 818 467" aria-hidden="true">
      <path d="M0 360 C240 338 420 405 560 436 C680 460 770 430 818 386 L818 408 C760 446 680 468 560 452 C420 432 250 382 0 386 Z" fill="#1b1a1c"/>
      <path d="M0 392 C220 376 420 418 560 444 C680 466 760 440 818 420 L818 467 L0 467 Z" fill="#2168b8"/>
    </svg>
    <p class="website">www.brightwayhaul.com.au</p>
  </section>

  <section class="card card--back" aria-label="Business card back">
    <h2 class="brand-name">Brightway Haul<br>&amp; Upkeep Services</h2>
    <h3 class="services-title">Services we offer</h3>
    <ul class="services-list">
      <li>Clean</li><li>Move</li>
      <li class="wide">General Maintenance And Repairs.</li>
    </ul>
  </section>

</main>
</body>
</html>
```